Corporate Business Card

Very professional, Modern, Not to busy, include phone address email, website
(253) 617-4930, 18761 52nd Avenue S, Kent, WA 98047, martin@plumlinegroup.com, varkoworks.com

Target Market(s)

Manufacturing

Industry/Entity Type

Aero, machining, manufacturing, Off road racing

Contact Information for Business Card

Phone, address email, website

```html
<!DOCTYPE html>
<html lang="en">
<head>
<meta charset="utf-8">
<title>Varko Works — Business Card</title>
<link href="https://fonts.googleapis.com/css2?family=Poppins:wght@400;500;700&display=swap" rel="stylesheet">
<style>
  :root {
    --backdrop: #2b2b2d;
    --brand-red: #d3222d;
    --brand-navy: #1d3a7a;
    --paper: #ffffff;
    --ink: #1b1b1b;
  }
  * { margin: 0; padding: 0; box-sizing: border-box; }
  html, body { width: 1200px; height: 960px; overflow: hidden; }
  body {
    background: var(--backdrop);
    font-family: "Poppins", sans-serif;
    position: relative;
  }
  .card {
    position: absolute;
    width: 700px;
    height: 400px;
    overflow: hidden;
    box-shadow: 0 10px 30px rgba(0,0,0,0.45);
  }
  .card-front { left: 70px; top: 50px; background: var(--brand-red); }
  .card-back { left: 430px; top: 510px; background: var(--paper); }

  .wordmark {
    position: absolute;
    font-weight: 700;
    font-size: 60px;
    letter-spacing: 1px;
    line-height: 1;
    white-space: nowrap;
  }
  .card-front .wordmark { left: 170px; top: 150px; color: var(--paper); }
  .card-front .wordmark-rule {
    position: absolute; left: 200px; top: 246px;
    width: 300px; height: 3px; background: var(--paper);
  }
  .card-back .wordmark { left: 330px; top: 60px; font-size: 50px; color: var(--brand-navy); }
  .card-back .wordmark-rule {
    position: absolute; left: 360px; top: 140px;
    width: 240px; height: 3px; background: var(--brand-navy);
  }

  .address {
    position: absolute; left: 50px; top: 170px;
    font-size: 17px; font-weight: 500; color: var(--ink); line-height: 1.4;
  }
  .contact-list {
    position: absolute; left: 50px; top: 240px;
    list-style: none; font-size: 16px; color: var(--ink); line-height: 1;
  }
  .contact-list li { display: flex; align-items: center; gap: 10px; margin-bottom: 10px; }
  .contact-list svg { width: 16px; height: 16px; flex: none; }

  .card-bands { position: absolute; left: 0; top: 0; width: 700px; height: 400px; }
  .band-url {
    position: absolute; right: 34px; bottom: 60px;
    font-size: 16px; font-weight: 500; color: var(--paper);
  }
</style>
</head>
<body>

  <section class="card card-front" aria-label="Card front">
    <div class="wordmark">Varko Works</div>
    <div class="wordmark-rule"></div>
  </section>

  <section class="card card-back" aria-label="Card back">
    <svg class="card-bands" viewBox="0 0 700 400" aria-hidden="true">
      <polygon points="0,330 490,330 488,338 0,338" fill="var(--brand-red)"/>
      <polygon points="0,346 486,346 474,400 0,400" fill="var(--brand-navy)"/>
      <polygon points="512,250 700,250 700,400 484,400" fill="var(--brand-red)"/>
    </svg>

    <div class="wordmark">Varko Works</div>
    <div class="wordmark-rule"></div>

    <p class="address">18761 52nd Avenue<br>S, Kent, WA 98047</p>

    <ul class="contact-list">
      <li>
        <svg viewBox="0 0 16 16"><path fill="var(--brand-red)" d="M3.5 1.5l2.5 0.5 1 3-1.6 1.2a8 8 0 0 0 4.4 4.4L11 9l3 1 0.5 2.5-2 2A11 11 0 0 1 1.5 3.5z"/></svg>
        (253) 617-4930
      </li>
      <li>
        <svg viewBox="0 0 16 16"><rect x="1" y="3" width="14" height="10" rx="1" fill="var(--brand-red)"/><path d="M1.5 4l6.5 5 6.5-5" stroke="#fff" stroke-width="1.3" fill="none"/></svg>
        martin@plumlinegroup.com
      </li>
      <li>
        <svg viewBox="0 0 16 16"><circle cx="8" cy="8" r="7" fill="var(--brand-red)"/><path d="M1 8h14M8 1c-3 3.5-3 10.5 0 14M8 1c3 3.5 3 10.5 0 14" stroke="#fff" stroke-width="1" fill="none"/></svg>
        www.varkoworks.com
      </li>
    </ul>

    <div class="band-url">www.varkoworks.com</div>
  </section>

</body>
</html>
```